Simple and clean

We need a business card design for a new company called Dwelling Hawk. It is a search engine to find current properties for sale or rent in New Zealand market.
We have already a colour scheme that we would like people to use.
Light brown: #D4CCB0
Light green: #D6E4D4
Green: #669966
Black/White
It is OK to divert from this colour scheme slightly as long as there is a green component to the business card.
Final design should be clean, simple and should communicate the nature of the business.
Target Market(s)
- First home buyers
- Real estate agents
- People seeking rentals
Industry/Entity Type
Business
Requirements
Must have
- Use those or similar colours.
Light brown: #D4CCB0
Light green: #D6E4D4
Green: #669966
Black/White

```html
<!DOCTYPE html>
<html lang="en">
<head>
<meta charset="utf-8">
<title>Dwelling Hawk – Business Card</title>
<link href="https://fonts.googleapis.com/css2?family=Arimo:wght@400;700&display=swap" rel="stylesheet">
<style>
  :root {
    --backdrop: #efefec;
    --green: #669966;
    --sage: #a9bf9c;
    --band-white: #ffffff;
    --band-grey: #e5e6e3;
    --ink-dark: #2c5a2c;
    --ink-soft: #46684a;
  }
  * { margin: 0; padding: 0; box-sizing: border-box; }
  html, body {
    width: 1200px;
    height: 2900px;
    overflow: hidden;
    background: var(--backdrop);
    font-family: "Arimo", Arial, sans-serif;
  }
  .card {
    position: absolute;
    left: 50px;
    top: 1136px;
    width: 1100px;
    height: 628px;
    background: var(--sage);
    overflow: hidden;
  }
  .band { position: absolute; top: 0; height: 100%; }
  .band--green-left { left: 0; width: 209px; background: var(--green); }
  .band--light-left { left: 209px; width: 132px; background: var(--band-white); }
  .band--light-right { left: 913px; width: 99px; background: var(--band-white); }
  .band--green-right { left: 1012px; width: 88px; background: var(--green); }
  .band__cap {
    position: absolute; left: 0; top: 0; width: 100%; height: 38%;
    background: var(--band-grey);
  }

  .brand {
    position: absolute;
    left: 380px;
    top: 236px;
    font-size: 24px;
    font-weight: 700;
    color: var(--ink-dark);
    white-space: nowrap;
  }

  .details {
    position: absolute;
    right: 280px;
    top: 62px;
    text-align: right;
    color: var(--ink-soft);
    white-space: nowrap;
  }
  .details__name {
    font-size: 40px; font-weight: 700; color: var(--ink-dark); line-height: 1.05;
  }
  .details__role {
    font-size: 24px; letter-spacing: 1px; margin-bottom: 60px;
  }
  .details__label {
    font-size: 22px; letter-spacing: 1px; line-height: 1.1; margin-top: 16px;
  }
  .details__value {
    font-size: 24px; font-weight: 700; color: var(--ink-dark); line-height: 1.15;
  }
  .details__web {
    font-size: 36px; font-weight: 700; color: var(--ink-dark); line-height: 1.2;
  }
</style>
</head>
<body>
  <section class="card" aria-label="Dwelling Hawk business card">
    <div class="band band--green-left"></div>
    <div class="band band--light-left"><div class="band__cap"></div></div>
    <div class="band band--light-right"><div class="band__cap"></div></div>
    <div class="band band--green-right"></div>

    <p class="brand">Dwelling Hawk</p>

    <div class="details">
      <p class="details__name">Alex Morgan</p>
      <p class="details__role">DIRECTOR</p>
      <p class="details__label">PHONE</p>
      <p class="details__value">000-000-0000</p>
      <p class="details__label">EMAIL</p>
      <p class="details__value">name@yourmail.com</p>
      <p class="details__label">WEBSITE</p>
      <p class="details__web">www.yourwebsite.com</p>
    </div>
  </section>
</body>
</html>
```